Business card design for a dynamic IT consulting company

We need a business card design for a young firm, specialized in the Telecommunications/Consulting industry. The name of the company is Quindor and Partners Business Consulting Ltd. (Short name: Quindor and Partnes)
Quindor = solve read reverse, so we aim to be uncomplicated and solution-oriented. The small pipe in our logo is also related to the word solve. So we need a new business card design, which is simple, eye catching and something non traditional (I would probably prefer a square shaped design rather than a rectangle, but open for suggestions). Attached our logo.

Target Market(s)

Usually our customers are Tier1 Telecoms providers (Q-Netra, Palorix, etc) and their executives.

Industry/Entity Type

Business

Contact Information for Business Card

Name: Bence Tolnavari
Email: b.tolnavari@quindor.hu
Web: www.quindor.hu
Mobile: +36 30 518 2769
Title: Managing Director

Optional:
Company name: Quindor and Partners Ltd.
Address: 1087 Budapest, Tolvenka str. 28/C, Hungary

Font styles to use
Other font styles liked:
• helveticaneue_medium, Prime Regular are used now.

Colors

Designer to choose colors to be used in the design.

Requirements
Must have
• I would like to have a 2 sided design.
Nice to have
• I thought if we make the logo a bit bigger (without the company name), that could go to the back with the company name below. I though, if the pipe in the logo is somehow touchable on the business card, would be nice and unique.

```html
<!DOCTYPE html>
<html lang="en">
<head>
<meta charset="utf-8">
<title>Quindor and Partners – Business Card</title>
<link href="https://fonts.googleapis.com/css2?family=Exo+2:wght@400;500&family=Work+Sans:wght@400&display=swap" rel="stylesheet">
<style>
  :root {
    --backdrop: #1d1d1f;
    --paper: #ffffff;
    --magenta: #b92f8f;
    --blue: #1a8fd6;
    --ink: #58585a;
    --ink-soft: #4a4a4c;
    --white: #ffffff;
  }
  * { margin: 0; padding: 0; box-sizing: border-box; }
  html, body { width: 1200px; height: 897px; overflow: hidden; background: var(--backdrop); }
  .canvas { position: relative; width: 1200px; height: 897px; }

  .card { position: absolute; left: 303px; width: 595px; height: 338px; }
  .card-front { top: 92px; background: var(--paper); }
  .card-back { top: 469px; background: var(--magenta); }

  .brand { position: absolute; display: flex; align-items: center; }
  .brand-square { width: 40px; height: 40px; margin-right: 18px; flex: none; }
  .brand-name {
    font-family: "Exo 2", sans-serif; font-weight: 400; font-size: 42px;
    line-height: 1; letter-spacing: -0.3px; white-space: nowrap;
  }

  .card-front .brand { left: 37px; top: 45px; }
  .card-front .brand-square { background: var(--magenta); }
  .card-front .brand-name { color: var(--ink); }

  .card-back .brand { left: 53px; top: 147px; }
  .card-back .brand-square { background: var(--white); }
  .card-back .brand-name { color: var(--white); }

  .person { position: absolute; left: 134px; top: 150px; }
  .person-name {
    font-family: "Exo 2", sans-serif; font-weight: 400; font-size: 22px;
    color: var(--blue); letter-spacing: 0.5px; line-height: 1.2;
  }
  .person-title {
    font-family: "Work Sans", sans-serif; font-size: 14px; color: var(--ink-soft); margin-top: 4px;
  }

  .contacts { position: absolute; left: 138px; top: 249px; list-style: none; }
  .contacts li {
    display: flex; align-items: center; height: 19px;
    font-family: "Work Sans", sans-serif; font-size: 13.5px; color: var(--ink-soft);
  }
  .contacts svg { width: 11px; height: 11px; margin-right: 13px; fill: var(--blue); flex: none; }

  .company { position: absolute; left: 350px; top: 254px; }
  .company-name {
    font-family: "Exo 2", sans-serif; font-weight: 500; font-size: 15px; color: var(--blue); line-height: 1.2;
  }
  .company-address {
    font-family: "Work Sans", sans-serif; font-size: 13.5px; color: var(--ink-soft); line-height: 17px; margin-top: 2px;
  }

  .back-web {
    position: absolute; left: 0; right: 0; top: 296px; text-align: center;
    font-family: "Work Sans", sans-serif; font-size: 15px; letter-spacing: 2px; color: var(--white);
  }
</style>
</head>
<body>
<main class="canvas">

  <section class="card card-front" aria-label="Card front">
    <div class="brand">
      <span class="brand-square"></span>
      <span class="brand-name">Quindor and Partners</span>
    </div>

    <div class="person">
      <p class="person-name">BENCE TOLNAVARI</p>
      <p class="person-title">Managing Director</p>
    </div>

    <ul class="contacts">
      <li>
        <svg viewBox="0 0 24 24" aria-hidden="true"><path d="M6.6 10.8a15.1 15.1 0 0 0 6.6 6.6l2.2-2.2a1 1 0 0 1 1-.25 11.4 11.4 0 0 0 3.6.57 1 1 0 0 1 1 1V20a1 1 0 0 1-1 1A17 17 0 0 1 3 4a1 1 0 0 1 1-1h3.5a1 1 0 0 1 1 1c0 1.25.2 2.45.57 3.57a1 1 0 0 1-.25 1z"/></svg>
        +36 30 518 2769
      </li>
      <li>
        <svg viewBox="0 0 24 24" aria-hidden="true"><path d="M2 5h20v14H2z M2 5l10 8 10-8" /></svg>
        b.tolnavari@quindor.hu
      </li>
      <li>
        <svg viewBox="0 0 24 24" aria-hidden="true"><path d="M12 2a10 10 0 1 0 0 20 10 10 0 0 0 0-20zm6.9 6h-3a15 15 0 0 0-1.3-4A8 8 0 0 1 18.9 8zM12 4a13 13 0 0 1 1.9 4h-3.8A13 13 0 0 1 12 4zM4.3 14a8 8 0 0 1 0-4h3.4a16 16 0 0 0 0 4zm.8 2h3a15 15 0 0 0 1.3 4A8 8 0 0 1 5.1 16zm3-8h-3a8 8 0 0 1 4.3-4A15 15 0 0 0 8.1 8zM12 20a13 13 0 0 1-1.9-4h3.8A13 13 0 0 1 12 20zm2.3-6H9.7a14 14 0 0 1 0-4h4.6a14 14 0 0 1 0 4zm.3 6a15 15 0 0 0 1.3-4h3a8 8 0 0 1-4.3 4zm1.7-6a16 16 0 0 0 0-4h3.4a8 8 0 0 1 0 4z"/></svg>
        www.quindor.hu
      </li>
    </ul>

    <div class="company">
      <p class="company-name">QUINDOR AND PARTNERS LTD.</p>
      <p class="company-address">1087 Budapest, Tolvenka<br>str. 28/C, Hungary</p>
    </div>
  </section>

  <section class="card card-back" aria-label="Card back">
    <div class="brand">
      <span class="brand-square"></span>
      <span class="brand-name">Quindor and Partners</span>
    </div>
    <p class="back-web">www.quindor.hu</p>
  </section>

</main>
</body>
</html>
```